Marta's Dwellings website

We need a simple website for our property investment business in the UK. We basically need our contact details and brief description.We have the company logo already done (via ArtFlockly) so please use these:https://drive.google.com/drive/folders/1szJ3iRhelElZ40NIFT7w-c14MaY3Y_oV?usp=sharingYou could use some stock photos of UK houses for now.Let me know when to provide more detailed descriptions, etc

Coding

Coded - Design and coding required

Number of Pages Required

1 page

Colors

Designer to choose colors to be used in the design.

```html
<!DOCTYPE html>
<html lang="en">
<head>
<meta charset="utf-8">
<title>Marta's Dwellings</title>
<link href="https://fonts.googleapis.com/css2?family=Montserrat:wght@300;400;500;600&family=Open+Sans:wght@400;600&display=swap" rel="stylesheet">
<style>
:root{
  --ink:#1d1d1d;
  --dark:#141414;
  --charcoal:#2b2b2b;
  --grey:#8a8a8a;
  --line:#cfcfcf;
  --paper:#ffffff;
  --accent:#f4b400;
  --text:#555555;
}
*{box-sizing:border-box;margin:0;padding:0}
html,body{width:1200px;height:3008px;overflow:hidden}
body{font-family:"Open Sans",Arial,sans-serif;color:var(--text);background:var(--paper);position:relative}
.display{font-family:"Montserrat",Arial,sans-serif}

/* header + hero */
.hero{position:absolute;left:0;top:0;width:1200px;height:660px;
  background:linear-gradient(180deg,#6f8db0 0%,#9fb3c6 30%,#8a4a38 55%,#5e3a2c 75%,#4e5a35 100%)}
.hero-shade{position:absolute;inset:0;background:rgba(0,0,0,.35)}
.topbar{position:absolute;top:0;left:0;width:1200px;height:96px}
.brand{position:absolute;left:60px;top:34px;display:flex;align-items:center;gap:10px;
  font-family:"Montserrat",Arial,sans-serif;font-weight:500;font-size:20px;letter-spacing:3px;color:var(--paper)}
.brand-mark{width:14px;height:14px;background:var(--paper)}
.main-nav{position:absolute;left:400px;top:70px;display:flex;gap:30px}
.main-nav a{font-family:"Montserrat",Arial,sans-serif;font-size:14px;color:var(--paper);text-decoration:none;letter-spacing:.5px}
.phone{position:absolute;right:64px;top:22px;display:flex;align-items:center;gap:8px;color:var(--paper);font-size:17px}
.hero-copy{position:absolute;left:0;top:260px;width:1200px;text-align:center;color:var(--paper)}
.hero-copy .kicker{font-family:"Montserrat",Arial,sans-serif;font-weight:300;font-size:46px;letter-spacing:6px}
.hero-copy h1{font-family:"Montserrat",Arial,sans-serif;font-weight:400;font-size:60px;letter-spacing:7px;margin-top:4px}
.btn-dark{display:inline-block;margin-top:26px;background:#111;color:var(--paper);font-family:"Montserrat",Arial,sans-serif;
  font-size:16px;letter-spacing:1px;padding:14px 38px}
.hero-edge{position:absolute;left:0;bottom:0}

/* about */
.about{position:absolute;left:0;top:740px;width:1200px;text-align:center}
.section-title{font-family:"Montserrat",Arial,sans-serif;font-weight:400;font-size:38px;letter-spacing:3px;color:var(--ink)}
.title-rule{width:520px;height:2px;background:var(--ink);margin:8px auto 18px}
.about p{width:620px;margin:0 auto 22px;font-size:15px;line-height:1.55}
.btn-outline{display:inline-block;border:1.5px solid var(--ink);color:var(--ink);font-family:"Montserrat",Arial,sans-serif;
  font-size:14px;letter-spacing:1px;padding:12px 30px;margin-top:10px}

/* services */
.services{position:absolute;left:0;top:1120px;width:1200px;height:620px;
  clip-path:polygon(0 14%,50% 0,100% 14%,100% 86%,50% 100%,0 86%);
  background:linear-gradient(180deg,#3a3a3a 0%,#565656 45%,#2a2a2a 100%)}
.services-title{position:absolute;left:0;top:112px;width:1200px;text-align:center;color:var(--paper)}
.services-title .title-rule{background:var(--paper);width:360px;margin-top:6px}
.service-row{position:absolute;left:160px;top:200px;display:flex;gap:40px}
.service-card{width:260px;height:280px;background:#9a9a9a;
  clip-path:polygon(50% 0,100% 24%,100% 100%,0 100%,0 24%);padding:5px}
.service-inner{width:100%;height:100%;background:#111;clip-path:polygon(50% 0,100% 24%,100% 100%,0 100%,0 24%);
  text-align:center;color:var(--paper);padding-top:58px}
.service-inner h3{font-family:"Montserrat",Arial,sans-serif;font-weight:400;font-size:17px;letter-spacing:1px;margin-top:8px}
.service-inner p{font-size:11px;line-height:1.4;width:180px;margin:6px auto 0;color:#cfcfcf}
.btn-small{display:inline-block;margin-top:16px;border:1px solid var(--paper);font-size:10px;letter-spacing:1px;padding:7px 18px;
  font-family:"Montserrat",Arial,sans-serif}

/* featured */
.featured{position:absolute;left:0;top:1770px;width:1200px}
.featured .section-title{text-align:center;font-size:32px}
.featured .title-rule{width:360px}
.listing-row{position:absolute;left:160px;top:72px;display:flex;gap:20px}
.listing{width:280px;background:var(--paper);box-shadow:0 3px 10px rgba(0,0,0,.18)}
.listing-photo{height:190px;background:linear-gradient(180deg,#8fb0d6 0%,#b8c9d8 35%,#9a4c37 60%,#6b3a2b 85%,#6e7a4a 100%)}
.listing-body{padding:16px 18px 22px}
.listing-body h4{font-family:"Montserrat",Arial,sans-serif;font-weight:500;font-size:15px;color:var(--ink)}
.listing-body p{font-size:11px;line-height:1.45;margin-top:6px;color:var(--grey)}
.btn-accent{display:inline-block;margin-top:14px;background:var(--accent);color:var(--ink);font-family:"Montserrat",Arial,sans-serif;
  font-size:10px;font-weight:600;letter-spacing:.5px;padding:8px 18px}
.arrow{position:absolute;top:180px}
.arrow.prev{left:112px}
.arrow.next{right:112px}

/* contact */
.contact{position:absolute;left:0;top:2290px;width:1200px;height:560px;
  clip-path:polygon(0 14%,50% 0,100% 14%,100% 100%,0 100%);
  background:linear-gradient(180deg,#4a4a4a 0%,#333 55%,#1a1a1a 100%)}
.contact-shade{position:absolute;inset:0;background:rgba(0,0,0,.35)}
.contact-copy{position:absolute;left:580px;top:110px;color:var(--paper)}
.contact-copy h2{font-family:"Montserrat",Arial,sans-serif;font-weight:400;font-size:30px;letter-spacing:3px}
.contact-copy .title-rule{background:var(--paper);width:440px;margin:8px 0 20px}
.contact-copy h3{font-family:"Montserrat",Arial,sans-serif;font-weight:600;font-size:17px;letter-spacing:1px;margin-bottom:14px}
.contact-line{display:flex;gap:14px;font-size:15px;line-height:1.45;margin-bottom:12px;width:420px}
.contact-line svg{flex:none;margin-top:2px}

/* footer */
.site-footer{position:absolute;left:0;top:2850px;width:1200px;height:158px;background:var(--dark);text-align:center;color:var(--paper)}
.footer-nav{display:flex;justify-content:center;gap:30px;padding-top:16px}
.footer-nav a{color:var(--paper);text-decoration:none;font-family:"Montserrat",Arial,sans-serif;font-size:14px}
.footer-rule{width:800px;height:1px;background:#555;margin:12px auto 8px}
.copyright{font-size:11px;color:#bbb}
.social{display:flex;justify-content:center;gap:18px;margin-top:10px}
.social span{width:14px;height:14px;border-radius:50%;background:#d8d8d8}
</style>
</head>
<body>

<header class="hero" role="img" aria-label="Photo of a red brick UK detached house on a residential street under a blue sky">
  <div class="hero-shade"></div>
  <div class="topbar">
    <div class="brand"><span class="brand-mark"></span>MARTA'S DWELLINGS</div>
    <nav class="main-nav">
      <a href="#">ABOUT US</a><a href="#">SERVICES</a><a href="#">WHY US</a><a href="#">OUR HOMES</a><a href="#">BLOGS</a><a href="#">CONTACT US</a>
    </nav>
    <div class="phone">
      <svg width="16" height="16" viewBox="0 0 24 24"><path fill="#fff" d="M6.6 10.8a15 15 0 0 0 6.6 6.6l2.2-2.2c.3-.3.7-.4 1-.2 1.1.4 2.3.6 3.6.6.6 0 1 .4 1 1V20c0 .6-.4 1-1 1A17 17 0 0 1 3 4c0-.6.4-1 1-1h3.5c.6 0 1 .4 1 1 0 1.3.2 2.5.6 3.6.1.3 0 .7-.2 1z"/></svg>
      665 555 0182
    </div>
  </div>
  <div class="hero-copy">
    <div class="kicker">WELCOME TO</div>
    <h1>MARTA'S DWELLINGS</h1>
    <span class="btn-dark">VIEW HOMES</span>
  </div>
  <svg class="hero-edge" width="1200" height="130" viewBox="0 0 1200 130">
    <polygon points="0,130 0,100 600,8 1200,100 1200,130" fill="#2a2a2a" opacity=".85"/>
    <polygon points="0,130 0,112 600,32 1200,112 1200,130" fill="#ffffff"/>
  </svg>
</header>

<section class="about">
  <h2 class="section-title">ABOUT MARTA'S DWELLINGS</h2>
  <div class="title-rule"></div>
  <p>Pellentesque faucibus Ut accumsan ultricies elit Maecenas at justo id velit placerat molestie Donec dictum lectus non odio Cras a ante vitae enim iaculis aliquam</p>
  <p>Mauris nunc quam venenatis nec euismod sit amet egestas placerat est Pellentesque habitant morbi tristique senectus et netus et malesuada fames ac turpis egestas Cras id elit Integer quis urna Ut Pellentesque faucibus Ut accumsan ultricies elit Maecenas</p>
  <span class="btn-outline">LEARN MORE</span>
</section>

<section class="services" role="img" aria-label="Muted dark photo of a row of UK houses behind the services panel">
  <div class="services-title">
    <h2 class="section-title" style="color:#fff">OUR SERVICES</h2>
    <div class="title-rule"></div>
  </div>
  <div class="service-row">
    <div class="service-card"><div class="service-inner">
      <svg width="40" height="40" viewBox="0 0 40 40" fill="none" stroke="#fff" stroke-width="2"><rect x="6" y="24" width="6" height="10"/><rect x="17" y="17" width="6" height="17"/><rect x="28" y="9" width="6" height="25"/><path d="M4 36h32"/></svg>
      <h3>INVESTMENT</h3>
      <p>Safe long-term returns from carefully chosen UK rental homes.</p>
      <span class="btn-small">LEARN MORE</span>
    </div></div>
    <div class="service-card"><div class="service-inner">
      <svg width="40" height="40" viewBox="0 0 40 40" fill="none" stroke="#fff" stroke-width="2"><path d="M5 19 20 6l15 13"/><path d="M9 16v18h22V16"/><rect x="17" y="23" width="6" height="11"/></svg>
      <h3>FIND HOME</h3>
      <p>We search the market to match you with the right property.</p>
      <span class="btn-small">LEARN MORE</span>
    </div></div>
    <div class="service-card"><div class="service-inner">
      <svg width="40" height="40" viewBox="0 0 40 40" fill="none" stroke="#fff" stroke-width="2"><path d="M5 19 20 6l15 13"/><path d="M9 16v18h22V16"/><circle cx="20" cy="24" r="3"/><path d="M20 27v5"/></svg>
      <h3>BUY HOME</h3>
      <p>Friendly support from first viewing through to collecting keys.</p>
      <span class="btn-small">LEARN MORE</span>
    </div></div>
  </div>
</section>

<section class="featured">
  <h2 class="section-title">FEATURED HOMES</h2>
  <div class="title-rule"></div>
  <svg class="arrow prev" width="16" height="34" viewBox="0 0 16 34"><path d="M14 2 2 17l12 15" fill="none" stroke="#999" stroke-width="2"/></svg>
  <svg class="arrow next" width="16" height="34" viewBox="0 0 16 34"><path d="M2 2l12 15L2 32" fill="none" stroke="#999" stroke-width="2"/></svg>
  <div class="listing-row">
    <article class="listing">
      <div class="listing-photo" role="img" aria-label="Photo of a terrace of new red brick homes"></div>
      <div class="listing-body"><h4>Duis nunc Nulla rhoncus</h4>
        <p>Three bedroom family home close to local schools and shops.</p>
        <span class="btn-accent">LEARN MORE</span></div>
    </article>
    <article class="listing">
      <div class="listing-photo" role="img" aria-label="Photo of a street of modern brick townhouses"></div>
      <div class="listing-body"><h4>Duis nunc Nulla rhoncus</h4>
        <p>Bright modern townhouse with private garden and driveway parking.</p>
        <span class="btn-accent">LEARN MORE</span></div>
    </article>
    <article class="listing">
      <div class="listing-photo" role="img" aria-label="Photo of a detached red brick house with a lawn"></div>
      <div class="listing-body"><h4>Duis nunc Nulla rhoncus</h4>
        <p>Spacious detached house on a quiet road near the park.</p>
        <span class="btn-accent">LEARN MORE</span></div>
    </article>
  </div>
</section>

<section class="contact" role="img" aria-label="Dark photo of suburban UK houses behind the contact details">
  <div class="contact-shade"></div>
  <div class="contact-copy">
    <h2>CONTACT US</h2>
    <div class="title-rule"></div>
    <h3>MARTA ELISE VANCE</h3>
    <div class="contact-line">
      <svg width="16" height="20" viewBox="0 0 16 20"><path fill="#fff" d="M8 0a7 7 0 0 0-7 7c0 5 7 13 7 13s7-8 7-13a7 7 0 0 0-7-7zm0 10a3 3 0 1 1 0-6 3 3 0 0 1 0 6z"/></svg>
      <span>Address - Unit 7, Harrow Court, 12-14 Willow Row, Fernby, Shireham, United Kingdom, FB4 9QX</span>
    </div>
    <div class="contact-line">
      <svg width="16" height="16" viewBox="0 0 24 24"><path fill="#fff" d="M6.6 10.8a15 15 0 0 0 6.6 6.6l2.2-2.2c.3-.3.7-.4 1-.2 1.1.4 2.3.6 3.6.6.6 0 1 .4 1 1V20c0 .6-.4 1-1 1A17 17 0 0 1 3 4c0-.6.4-1 1-1h3.5c.6 0 1 .4 1 1 0 1.3.2 2.5.6 3.6.1.3 0 .7-.2 1z"/></svg>
      <span>986.555.0147</span>
    </div>
    <div class="contact-line">
      <svg width="16" height="14" viewBox="0 0 16 14"><rect x="1" y="1" width="14" height="12" fill="none" stroke="#fff" stroke-width="1.5"/><path d="M1 1l7 6 7-6" fill="none" stroke="#fff" stroke-width="1.5"/></svg>
      <span>info@martasdwellings.example</span>
    </div>
  </div>
</section>

<footer class="site-footer">
  <nav class="footer-nav">
    <a href="#">HOME</a><a href="#">ABOUT US</a><a href="#">SERVICES</a><a href="#">WHY US</a><a href="#">OUR HOMES</a><a href="#">BLOGS</a><a href="#">CONTACT US</a>
  </nav>
  <div class="footer-rule"></div>
  <div class="copyright">© 2019 Company Name. All right reserved.</div>
  <div class="social"><span></span><span></span><span></span><span></span></div>
</footer>

</body>
</html>
```